Quick Straightforward Billboard Redesign

- Design billboard sized for 10 foot' x 36' foot width live area size and please include bleeds 6" around all sides
- Exact blue color match is imperative in headline, logo, phone number bubble or wherever used. C-83 / M-45 / Y-1 / K-0-
- What I hope to illustrate is that our company offers the best porch screening in the area area, in regards to quality, expertise, durability, storms proof, but we do not build screen porches.
- Current board is attached below from previous designer, and as you can see sizing was off, white space on edges make it appear to be sized incorrectly.
- I also attached my own little mock up idea well well if it helps, favorite image, logo, headline, etc and ideas perhaps on expanding or making this better?

Thanks so much!

Target Market(s)

Drivers and passengers, Southeastern NC, are of immense new construction and high end homes.

Industry/Entity Type

Construction

Colors
0054AA
0677BA
7BADD7
CADEEF
E8F1F8

Requirements
Must have
• Blue color matching
Nice to have
• Design spins or other thoughts on my little mock up

```html
<!DOCTYPE html>
<html lang="en">
<head>
<meta charset="utf-8">
<title>Porch Screening Billboard</title>
<link rel="stylesheet" href="https://fonts.googleapis.com/css2?family=Arimo:ital,wght@0,700;1,700&display=swap">
<style>
  :root {
    --brand-blue: #0054AA;
    --mid-blue: #0677BA;
    --soft-blue: #7BADD7;
    --pale-blue: #CADEEF;
    --mist-blue: #E8F1F8;
    --headline-green: #1BA64F;
    --panel-white: #FFFFFF;
    --stage: #EEF2F6;
  }
  * { margin: 0; padding: 0; box-sizing: border-box; }
  html, body {
    width: 1200px;
    height: 899px;
    overflow: hidden;
    background: var(--stage);
  }
  .billboard {
    position: absolute;
    left: 20px;
    top: 289px;
    width: 1160px;
    height: 322px;
    display: flex;
    background: var(--panel-white);
    box-shadow: 0 6px 18px rgba(0, 40, 90, 0.18);
  }
  .message-panel {
    position: relative;
    width: 500px;
    height: 100%;
    overflow: hidden;
    background: var(--panel-white);
    font-family: "Arimo", Arial, sans-serif;
  }
  .headline {
    position: absolute;
    left: 38px;
    font-weight: 700;
    font-style: italic;
    font-size: 44px;
    line-height: 1.1;
    letter-spacing: 0.5px;
    white-space: nowrap;
  }
  .headline--screen { top: 38px; color: var(--headline-green); }
  .headline--coast { top: 118px; color: var(--brand-blue); }
  .brand-name {
    position: absolute;
    left: 38px;
    top: 236px;
    display: flex;
    align-items: center;
    gap: 12px;
    font-weight: 700;
    font-size: 33px;
    line-height: 1;
    color: var(--brand-blue);
    text-transform: uppercase;
    white-space: nowrap;
  }
  .brand-mark {
    width: 30px;
    height: 30px;
    flex: none;
    background: var(--mid-blue);
  }
  .porch-photo {
    position: relative;
    flex: 1;
    height: 100%;
  }
  .porch-photo svg { display: block; width: 100%; height: 100%; }
  .phone-bubble {
    position: absolute;
    left: 52px;
    top: 198px;
    width: 560px;
    height: 92px;
    border-radius: 46px;
    background: var(--brand-blue);
    color: var(--panel-white);
    font-family: "Arimo", Arial, sans-serif;
    font-weight: 700;
    font-size: 62px;
    letter-spacing: 1px;
    display: flex;
    align-items: center;
    justify-content: center;
  }
</style>
</head>
<body>
  <section class="billboard">
    <div class="message-panel">
      <p class="headline headline--screen">Screen Your Porch.</p>
      <p class="headline headline--coast">Built for the Coast.</p>
      <div class="brand-name"><span class="brand-mark"></span>Tidewater Screens</div>
    </div>
    <div class="porch-photo">
      <svg role="img" aria-label="Photo of a screened coastal porch with wicker seating, ceiling fans and a lake view" viewBox="0 0 660 322" preserveAspectRatio="none">
        <defs>
          <linearGradient id="porchTones" x1="0" y1="0" x2="0" y2="1">
            <stop offset="0" stop-color="#F4F5F6"/>
            <stop offset="0.3" stop-color="#DDE3E8"/>
            <stop offset="0.42" stop-color="#9CC3E4"/>
            <stop offset="0.55" stop-color="#7E9A6A"/>
            <stop offset="0.7" stop-color="#8A8378"/>
            <stop offset="1" stop-color="#C9C6C0"/>
          </linearGradient>
        </defs>
        <rect width="660" height="322" fill="url(#porchTones)"/>
      </svg>
      <div class="phone-bubble">910.555.0142</div>
    </div>
  </section>
</body>
</html>
```